Website for a new t-shirt company called bolddawnapperal.com

We are looking for a talented web designer to create a website that aligns with our brand's message and identity centered around the theme of "Bold Dawn." The website should be modern, clean, and visually appealing while also being user-friendly and easy to navigate.

We will be using the Big Commerce platform for our online store section, so the designer should have experience in designing websites on this platform.

We would like the website to have the following elements:

A color scheme that aligns with the brand's identity and message
A homepage that showcases our products and message, with clear calls-to-action for visitors to explore further
A blog section that highlights our brand's philosophy and offers advice and tips for people looking to make positive changes in their lives
An "About Us" section that introduces our brand and team and offers insight into our mission and values
A contact form that allows visitors to easily get in touch with us for inquiries or support
We are open to creative suggestions and ideas from the designer, but we would like the website to have a modern and minimalist aesthetic that resonates with our target audience of 20 to 40-year-olds.

```html
<!DOCTYPE html>
<html lang="en">
<head>
<meta charset="utf-8">
<title>Bold Dawn – T-Shirts</title>
<link href="https://fonts.googleapis.com/css2?family=Poppins:wght@300;400;500;600&display=swap" rel="stylesheet">
<style>
:root{
  --ink:#111111;
  --text:#333333;
  --muted:#555555;
  --line:#dcdcdc;
  --paper:#ffffff;
  --soft:#f0f0f0;
  --hero-a:#e4e1de;
  --hero-b:#cfcac6;
  --dark:#1b1b1b;
}
*{box-sizing:border-box;margin:0;padding:0}
html,body{width:1200px;height:4823px;overflow:hidden}
body{position:relative;background:var(--paper);font-family:'Poppins',sans-serif;color:var(--text)}
.abs{position:absolute}
a{color:inherit;text-decoration:none}
.btn{position:absolute;display:flex;align-items:center;justify-content:center;background:var(--ink);color:#fff;font-family:'Poppins',sans-serif}
.btn-outline{background:#fff;color:var(--ink);border:2px solid var(--ink)}
.rule{position:absolute;height:3px;background:var(--ink)}
.section-title{position:absolute;left:0;width:1200px;text-align:center;font-weight:600;font-size:40px;color:var(--ink)}

/* header + hero */
.hero{left:0;top:0;width:1200px;height:755px;background:linear-gradient(100deg,var(--hero-b) 0%,var(--hero-a) 45%,#dcd9d6 100%)}
.hero-photo{left:30px;top:170px;width:560px;height:585px;background:linear-gradient(180deg,#d6d2ce 0%,#c7c1bc 60%,#bdb6b0 100%);border-radius:0}
.logo{left:82px;top:44px;font-size:44px;font-weight:500;color:var(--ink);letter-spacing:.5px}
.nav{left:0;top:52px;font-size:15px;color:var(--ink)}
.nav span{position:absolute;white-space:nowrap}
.nav-shop{left:870px;top:45px;width:90px;height:36px;font-size:14px}
.icons svg{position:absolute;top:49px}
.hero-title{left:698px;top:340px;font-size:44px;font-weight:600;color:var(--ink);white-space:nowrap}
.hero-sub{left:721px;top:406px;font-size:19px;color:var(--ink);white-space:nowrap}
.hero-cta{left:777px;top:492px;width:176px;height:58px;font-size:19px;gap:12px}

/* categories */
.cat{top:870px;width:316px;height:263px;background:linear-gradient(90deg,#d7d3cf 0%,#e8e6e4 45%,#f4f4f4 60%,#f7f7f7 100%)}
.cat-label{position:absolute;right:24px;top:92px;text-align:center;font-size:27px;line-height:32px;color:var(--ink);width:150px}
.cat .btn{right:50px;top:188px;width:88px;height:36px;font-size:18px}

/* tabs */
.tab{top:1387px;width:227px;height:75px;font-size:19px}

/* products */
.card{top:1526px;width:320px;height:468px;border:1px solid var(--line);background:#fff}
.card-img{position:absolute;left:0;top:0;width:318px;height:252px;background:linear-gradient(180deg,#e9ebee 0%,#dfe2e6 100%)}
.card h3{position:absolute;top:279px;width:100%;text-align:center;font-weight:400;font-size:17px;color:var(--ink)}
.card p{position:absolute;top:312px;width:100%;text-align:center;font-size:14px;line-height:18px;color:var(--muted)}
.card .dots{position:absolute;left:34px;right:34px;top:377px;border-top:1px dashed #777}
.card .price{position:absolute;left:34px;top:394px;font-size:17px;color:var(--ink)}
.card .tools{position:absolute;right:30px;top:396px;display:flex;gap:24px}
.card .btn{left:122px;top:442px;width:86px;height:38px;font-size:16px}
.arrow{width:48px;height:48px;border-radius:50%;background:#fff;box-shadow:0 2px 8px rgba(0,0,0,.15);display:flex;align-items:center;justify-content:center}

/* about */
.about{left:0;top:2130px;width:1200px;height:768px;background:var(--soft)}
.frame{left:60px;top:2220px;width:292px;height:326px;border:3px solid var(--ink)}
.about-photo1{left:97px;top:2260px;width:334px;height:361px;background:linear-gradient(180deg,#9aa0a3 0%,#8b8f86 50%,#d8d4cf 100%)}
.about-photo2{left:309px;top:2417px;width:258px;height:281px;background:#fff;padding:8px}
.about-photo2 div{width:100%;height:100%;background:linear-gradient(90deg,#dcdcdc 0%,#efefef 100%)}
.about-title{left:637px;top:2218px;font-size:40px;font-weight:600;color:var(--ink)}
.about-text{left:637px;top:2338px;width:446px;font-size:15px;line-height:25.8px;color:var(--muted);text-align:justify}

/* features */
.feature{top:2853px;width:210px;text-align:center}
.feature .ring{width:104px;height:104px;margin:0 auto;border-radius:50%;background:#fff;border:2px solid #ddd;box-shadow:inset 0 0 0 6px #fff,0 0 0 1px #eee;display:flex;align-items:center;justify-content:center}
.feature span{display:block;margin-top:18px;font-size:17px;color:var(--ink)}

/* blog */
.post{top:3239px;width:318px;height:370px}
.post-img{position:absolute;left:0;top:0;width:316px;height:282px}
.post-box{position:absolute;left:0;top:191px;width:249px;height:174px;background:#fff;padding:22px 0 0 34px}
.post-box .date{font-size:11px;color:var(--text);display:flex;align-items:center;gap:6px}
.post-box h4{margin-top:10px;font-size:18px;font-weight:600;color:var(--ink)}
.post-box p{margin-top:8px;font-size:12px;line-height:19px;color:var(--text)}
.post-box a{display:block;margin-top:14px;font-size:13px;font-style:normal;text-decoration:underline;color:var(--text)}

/* contact */
.contact-title{left:84px;top:3705px;font-size:40px;font-weight:600;color:var(--ink)}
.field{height:51px;background:#fff;box-shadow:0 2px 10px rgba(0,0,0,.12);display:flex;align-items:center;gap:10px;padding-left:20px;font-size:16px;color:#8a8a8a}
.field.msg{align-items:flex-start;padding-top:14px;height:101px}
.contact-img{left:696px;top:3697px;width:412px;height:496px;background:linear-gradient(90deg,#c9c4bd 0%,#e8e6e3 40%,#6b3a2e 80%,#4a2a22 100%)}

/* newsletter + footer */
.footer{left:0;top:4371px;width:1200px;height:452px;background:var(--dark)}
.news{left:204px;top:4310px;width:760px;height:248px;background:#fff}
.news-title{left:0;top:4320px;width:1200px;text-align:center;font-size:40px;font-weight:500;color:var(--ink)}
.news-text{left:0;top:4374px;width:1200px;text-align:center;font-size:15px;line-height:23px;color:var(--ink)}
.news-input{left:335px;top:4440px;width:539px;height:75px;background:#ebebeb}
.news-submit{left:775px;top:4455px;width:86px;height:47px;font-size:15px}
.foot-nav span{position:absolute;top:4643px;font-size:14px;color:#fff;white-space:nowrap}
.foot-sep{top:4630px;width:2px;height:30px;background:#fff}
.social{top:4620px;width:34px;height:34px;border:1.5px solid #fff;border-radius:50%}
.foot-line{left:86px;top:4693px;width:1030px;height:1px;background:#fff}
.copy{top:4728px;font-size:15px;color:#fff;white-space:nowrap}
.pay{top:4729px;width:30px;height:19px;border-radius:2px}
</style>
</head>
<body>

<!-- Hero -->
<div class="abs hero"></div>
<div class="abs hero-photo" role="img" aria-label="Smiling woman in a white tee holding up a black t-shirt on a hanger"></div>
<div class="abs logo">Bold Dawn</div>
<nav class="abs nav">
  <span style="left:362px">Home</span>
  <span style="left:450px">About Us</span>
  <span style="left:560px">Products ▾</span>
  <span style="left:669px">Blog</span>
  <span style="left:743px">Contact Us</span>
</nav>
<a class="btn nav-shop">Shop</a>
<div class="icons">
  <svg style="left:990px" width="20" height="20" viewBox="0 0 20 20" fill="none" stroke="#111" stroke-width="1.6"><circle cx="10" cy="10" r="8.5"/><circle cx="10" cy="8" r="3"/><path d="M4.5 16c1.5-2.5 3.3-3.5 5.5-3.5s4 1 5.5 3.5"/></svg>
  <svg style="left:1030px" width="20" height="20" viewBox="0 0 20 20" fill="none" stroke="#111" stroke-width="2"><circle cx="8" cy="8" r="5.5"/><path d="M12 12l6 6"/></svg>
  <svg style="left:1063px" width="22" height="20" viewBox="0 0 22 20" fill="none" stroke="#111" stroke-width="1.8"><path d="M11 18S2 12.5 2 6.8A4.6 4.6 0 0 1 11 4.8a4.6 4.6 0 0 1 9 2C20 12.5 11 18 11 18z"/></svg>
  <svg style="left:1096px" width="22" height="20" viewBox="0 0 22 20" fill="none" stroke="#111" stroke-width="1.6"><path d="M1 2h3l3 11h11l2-8H6"/><circle cx="8" cy="17" r="1.5"/><circle cx="17" cy="17" r="1.5"/></svg>
</div>
<h1 class="abs hero-title">Trendy T-Shirts</h1>
<p class="abs hero-sub">Up to 50% Offer On Top- Brands</p>
<a class="btn hero-cta">Shop Now
  <svg width="30" height="12" viewBox="0 0 30 12" fill="none" stroke="#fff" stroke-width="1.6"><path d="M0 6h28M23 1l5 5-5 5"/></svg>
</a>

<!-- Categories -->
<div class="abs cat" style="left:73px">
  <div class="abs" role="img" aria-label="T-shirts hanging on a clothes rail" style="left:0;top:0;width:160px;height:263px;background:linear-gradient(90deg,#6f7a6c,#8c9486,#c97a4e,#e2ded8)"></div>
  <div class="cat-label">Designer<br>T-Shirt</div><a class="btn">shop</a>
</div>
<div class="abs cat" style="left:434px">
  <div class="abs" role="img" aria-label="T-shirts hanging on a clothes rail" style="left:0;top:0;width:160px;height:263px;background:linear-gradient(90deg,#6f8a72,#7d9480,#c2593b,#e4e1dd)"></div>
  <div class="cat-label">Branded<br>T-Shirt</div><a class="btn">shop</a>
</div>
<div class="abs cat" style="left:792px">
  <div class="abs" role="img" aria-label="T-shirts hanging on a clothes rail" style="left:0;top:0;width:160px;height:263px;background:linear-gradient(90deg,#6f8a72,#7d9480,#c2593b,#e4e1dd)"></div>
  <div class="cat-label">Casual<br>T-Shirt</div><a class="btn">shop</a>
</div>

<!-- Products -->
<h2 class="section-title" style="top:1237px">Our Products</h2>
<div class="rule" style="left:572px;top:1306px;width:56px"></div>
<a class="btn tab" style="left:219px">Best Collections</a>
<a class="btn btn-outline tab" style="left:487px">New Arrivals</a>
<a class="btn btn-outline tab" style="left:753px">Best Offers</a>

<div class="abs arrow" style="left:25px;top:1627px"><svg width="10" height="14" viewBox="0 0 10 14" fill="none" stroke="#111" stroke-width="2.2"><path d="M8 1L2 7l6 6"/></svg></div>
<div class="abs arrow" style="left:1127px;top:1627px"><svg width="10" height="14" viewBox="0 0 10 14" fill="none" stroke="#111" stroke-width="2.2"><path d="M2 1l6 6-6 6"/></svg></div>

<div class="abs card" style="left:88px">
  <div class="card-img" role="img" aria-label="Plain white t-shirt" style="background:linear-gradient(180deg,#f2f3f5,#e3e5e8)"></div>
  <h3>Best Collection 1</h3><p>Lorum Ipsum Dolor<br>Sit Amet</p><div class="dots"></div><div class="price">$54.90</div>
  <div class="tools">
    <svg width="16" height="16" viewBox="0 0 16 16" fill="none" stroke="#111" stroke-width="1.8"><circle cx="6.5" cy="6.5" r="4.5"/><path d="M10 10l5 5"/></svg>
    <svg width="17" height="15" viewBox="0 0 22 20" fill="none" stroke="#111" stroke-width="2"><path d="M11 18S2 12.5 2 6.8A4.6 4.6 0 0 1 11 4.8a4.6 4.6 0 0 1 9 2C20 12.5 11 18 11 18z"/></svg>
    <svg width="17" height="15" viewBox="0 0 22 20" fill="none" stroke="#111" stroke-width="1.8"><path d="M1 2h3l3 11h11l2-8H6"/><circle cx="8" cy="17" r="1.5"/><circle cx="17" cy="17" r="1.5"/></svg>
  </div>
  <a class="btn">Shop</a>
</div>
<div class="abs card" style="left:438px">
  <div class="card-img" role="img" aria-label="Model wearing a black oversized t-shirt"></div>
  <h3>Best Collection 2</h3><p>Lorum Ipsum Dolor<br>Sit Amet</p><div class="dots"></div><div class="price">$54.90</div>
  <div class="tools">
    <svg width="16" height="16" viewBox="0 0 16 16" fill="none" stroke="#111" stroke-width="1.8"><circle cx="6.5" cy="6.5" r="4.5"/><path d="M10 10l5 5"/></svg>
    <svg width="17" height="15" viewBox="0 0 22 20" fill="none" stroke="#111" stroke-width="2"><path d="M11 18S2 12.5 2 6.8A4.6 4.6 0 0 1 11 4.8a4.6 4.6 0 0 1 9 2C20 12.5 11 18 11 18z"/></svg>
    <svg width="17" height="15" viewBox="0 0 22 20" fill="none" stroke="#111" stroke-width="1.8"><path d="M1 2h3l3 11h11l2-8H6"/><circle cx="8" cy="17" r="1.5"/><circle cx="17" cy="17" r="1.5"/></svg>
  </div>
  <a class="btn">Shop</a>
</div>
<div class="abs card" style="left:786px">
  <div class="card-img" role="img" aria-label="Model wearing a white t-shirt"></div>
  <h3>Best Collection 1</h3><p>Lorum Ipsum Dolor<br>Sit Amet</p><div class="dots"></div><div class="price">$54.90</div>
  <div class="tools">
    <svg width="16" height="16" viewBox="0 0 16 16" fill="none" stroke="#111" stroke-width="1.8"><circle cx="6.5" cy="6.5" r="4.5"/><path d="M10 10l5 5"/></svg>
    <svg width="17" height="15" viewBox="0 0 22 20" fill="none" stroke="#111" stroke-width="2"><path d="M11 18S2 12.5 2 6.8A4.6 4.6 0 0 1 11 4.8a4.6 4.6 0 0 1 9 2C20 12.5 11 18 11 18z"/></svg>
    <svg width="17" height="15" viewBox="0 0 22 20" fill="none" stroke="#111" stroke-width="1.8"><path d="M1 2h3l3 11h11l2-8H6"/><circle cx="8" cy="17" r="1.5"/><circle cx="17" cy="17" r="1.5"/></svg>
  </div>
  <a class="btn">Shop</a>
</div>

<!-- About -->
<div class="abs about"></div>
<div class="abs frame"></div>
<div class="abs about-photo1" role="img" aria-label="Woman in a sage green t-shirt"></div>
<div class="abs about-photo2"><div role="img" aria-label="Black t-shirt on a hanger against a white wall"></div></div>
<h2 class="abs about-title">About Us</h2>
<div class="rule" style="left:637px;top:2286px;width:56px"></div>
<p class="abs about-text">Lorem ipsum dolor sit amet, consectetur adipiscing elit, sed do eiusmodtempor incididunt ut labore et dolore magnaaliquaUt enim ad minim  Lorem ipsum dolor sit amet, consectetur adipiscing elit,sed do eiusmod tempor incididunt ut labore et dolore magna aliquaUt enim ad minim. consectetur adipi scing elit,sed do eiusmod tempor incididunt ut labore et dolore</p>
<a class="btn" style="left:646px;top:2576px;width:178px;height:71px;font-size:17px">Know More</a>
<a class="btn btn-outline" style="left:835px;top:2576px;width:180px;height:71px;font-size:17px">Shop Now</a>

<!-- Features -->
<div class="abs feature" style="left:202px">
  <div class="ring"><svg width="64" height="40" viewBox="0 0 64 40"><rect x="2" y="4" width="38" height="24" rx="2" fill="#111"/><path d="M40 12h12l8 9v7H40z" fill="#111"/><rect x="44" y="14" width="8" height="6" fill="#fff"/><circle cx="14" cy="31" r="5" fill="#111" stroke="#fff" stroke-width="2"/><circle cx="50" cy="31" r="5" fill="#111" stroke="#fff" stroke-width="2"/><text x="8" y="20" font-family="Poppins,sans-serif" font-size="10" font-weight="600" font-style="normal" fill="#fff">FREE</text></svg></div>
  <span>Free Delivery</span>
</div>
<div class="abs feature" style="left:397px">
  <div class="ring"><svg width="50" height="52" viewBox="0 0 50 52" fill="none" stroke="#111" stroke-width="3"><path d="M10 24a15 15 0 0 1 30 0"/><rect x="6" y="22" width="7" height="12" rx="3" fill="#111"/><rect x="37" y="22" width="7" height="12" rx="3" fill="#111"/><circle cx="25" cy="25" r="9" fill="#111"/><path d="M8 50c2-9 9-12 17-12s15 3 17 12z" fill="#111"/></svg></div>
  <span>24/7 Support</span>
</div>
<div class="abs feature" style="left:586px">
  <div class="ring"><svg width="60" height="60" viewBox="0 0 60 60" fill="none" stroke="#111" stroke-width="3.5"><path d="M48 18A22 22 0 1 1 30 8"/><path d="M24 3l7 5-6 6" stroke-width="3"/><text x="17" y="35" font-family="Poppins,sans-serif" font-size="11" fill="#111" stroke="none">100%</text></svg></div>
  <span>100% Return</span>
</div>
<div class="abs feature" style="left:775px">
  <div class="ring"><svg width="46" height="52" viewBox="0 0 46 52"><path d="M23 2l20 8v14c0 14-9 22-20 26C12 46 3 38 3 24V10z" fill="#111"/><path d="M14 26l7 7 12-13" fill="none" stroke="#fff" stroke-width="4"/></svg></div>
  <span>100% Reliability</span>
</div>

<!-- Blog -->
<h2 class="section-title" style="top:3092px">Our Blog</h2>
<div class="rule" style="left:567px;top:3160px;width:66px"></div>

<div class="abs post" style="left:86px">
  <div class="post-img" role="img" aria-label="Group of friends in black t-shirts posing outdoors" style="background:linear-gradient(180deg,#dfe8d4 0%,#9bb46f 55%,#5f7d3a 100%)"></div>
  <div class="post-box"><div class="date"><svg width="10" height="10" viewBox="0 0 10 10" fill="none" stroke="#333"><rect x="1" y="2" width="8" height="7"/><path d="M1 4h8M3 1v2M7 1v2"/></svg>July 25, 2023</div><h4>Post 1 Headline</h4><p>Lorem ipsum dolor sit amet,<br>consectetur adipi</p><a>Read More</a></div>
</div>
<div class="abs post" style="left:442px">
  <div class="post-img" role="img" aria-label="Young friends in dark t-shirts outdoors in sunlight" style="background:linear-gradient(180deg,#d9c98c 0%,#a5a06a 50%,#4e5a3a 100%)"></div>
  <div class="post-box"><div class="date"><svg width="10" height="10" viewBox="0 0 10 10" fill="none" stroke="#333"><rect x="1" y="2" width="8" height="7"/><path d="M1 4h8M3 1v2M7 1v2"/></svg>July 25, 2023</div><h4>Post 2 Headline</h4><p>Lorem ipsum dolor sit amet,<br>consectetur adipi</p><a>Read More</a></div>
</div>
<div class="abs post" style="left:799px">
  <div class="post-img" role="img" aria-label="Friends in casual t-shirts sitting on grass" style="background:linear-gradient(180deg,#f1ead8 0%,#c9b99a 40%,#5d6f8a 75%,#7c9a5a 100%)"></div>
  <div class="post-box"><div class="date"><svg width="10" height="10" viewBox="0 0 10 10" fill="none" stroke="#333"><rect x="1" y="2" width="8" height="7"/><path d="M1 4h8M3 1v2M7 1v2"/></svg>July 25, 2023</div><h4>Post 3 Headline</h4><p>Lorem ipsum dolor sit amet,<br>consectetur adipi</p><a>Read More</a></div>
</div>

<!-- Contact -->
<h2 class="abs contact-title">Contact Us</h2>
<div class="rule" style="left:92px;top:3778px;width:72px"></div>
<div class="abs field" style="left:92px;top:3866px;width:247px"><svg width="12" height="14" viewBox="0 0 12 14" fill="#333"><circle cx="6" cy="4" r="3.5"/><path d="M0 14c0-4 3-6 6-6s6 2 6 6z"/></svg>Your Name</div>
<div class="abs field" style="left:361px;top:3866px;width:247px"><svg width="13" height="13" viewBox="0 0 14 14" fill="none" stroke="#333" stroke-width="1.6"><path d="M3 1l3 3-2 2a8 8 0 0 0 4 4l2-2 3 3-2 2C6 13 1 8 1 3z"/></svg>Phone Number</div>
<div class="abs field" style="left:92px;top:3942px;width:247px"><svg width="13" height="10" viewBox="0 0 13 10" fill="#333"><rect width="13" height="10" rx="1"/><path d="M1 1l5.5 5L12 1" fill="none" stroke="#fff" stroke-width="1.2"/></svg>Email Address</div>
<div class="abs field" style="left:361px;top:3942px;width:247px"><svg width="10" height="14" viewBox="0 0 10 14" fill="#333"><path d="M5 0a5 5 0 0 1 5 5c0 4-5 9-5 9S0 9 0 5a5 5 0 0 1 5-5z"/><circle cx="5" cy="5" r="2" fill="#fff"/></svg>Address</div>
<div class="abs field msg" style="left:92px;top:4021px;width:516px"><svg width="13" height="13" viewBox="0 0 14 14" fill="#333" style="margin-top:4px"><path d="M7 1c3.5 0 6 2.3 6 5s-2.5 5-6 5l-4 2 1-3C2 9 1 7.8 1 6c0-2.7 2.5-5 6-5z"/></svg>Message</div>
<a class="btn" style="left:288px;top:4160px;width:137px;height:52px;font-size:18px">Submit</a>
<div class="abs contact-img" role="img" aria-label="White t-shirt on a hanger in front of a dark wooden cabinet with a flower vase"></div>

<!-- Newsletter + footer -->
<div class="abs footer"></div>
<div class="abs news"></div>
<h2 class="abs news-title">Let's Keep In Touch</h2>
<p class="abs news-text">Sign up for our newsletter to receive news<br>&amp; other information about discounts.</p>
<div class="abs news-input"></div>
<a class="btn news-submit">Submit</a>

<div class="foot-nav">
  <span style="left:99px">ABOUT US</span>
  <span style="left:238px">OUR STORY</span>
  <span style="left:382px">SHOP</span>
  <span style="left:472px">BLOG</span>
  <span style="left:577px">CONTACT</span>
</div>
<div class="abs foot-sep" style="left:206px"></div>
<div class="abs foot-sep" style="left:354px"></div>
<div class="abs foot-sep" style="left:451px"></div>
<div class="abs foot-sep" style="left:554px"></div>
<div class="abs social" style="left:971px"></div>
<div class="abs social" style="left:1012px"></div>
<div class="abs social" style="left:1053px"></div>
<div class="abs social" style="left:1094px"></div>
<div class="abs foot-line"></div>
<p class="abs copy" style="left:98px">Copyright © 2023 All Rights Reserved By Company</p>
<p class="abs copy" style="left:605px">Terms &amp; Conditions &nbsp;|&nbsp; Privacy Policy</p>
<div class="abs pay" style="left:992px;background:#3b6fb6"></div>
<div class="abs pay" style="left:1027px;background:#2a5bb0"></div>
<div class="abs pay" style="left:1062px;background:#e0832c"></div>
<div class="abs pay" style="left:1097px;background:#3a8fd0"></div>

</body>
</html>
```